New Business Card Design for Manufacturing

We are an engineering/manufacturing company that offers Advanced machining/assembly/engineering services, as well as innovative products for the heavy duty engine cooling markets.

We are looking to get a new business card designed that is clean and modern looking, but still fits the wide range of technical/skilled work we do.

- We hope to use this design as the base for other design work in new Presentations, web, and print work.

Industry/Entity Type

Engineering

Contact Information for Business Card

Our preferred color of blue is (RGB) 22/71/159 but can vary slightly from that color. Our content will be our Logo and full company name (Vantrell Forge Works, Inc.), company address, name, job title, phone number with extension, cell number, fax number, website, and email address on the cards.
We'd like the full company name next to the logo, but we are open to other interpretations of that layout.
Preferably, we would like the back side to be clean with just our logo, and the front to contain all of the contact information.

Colors
2f74b4
0355a3
85abd2

Requirements
Must have
• - Logo, company name, needed content - We are open to interpretation beyond that.
• - Standard size business card.
• - Horizontal orientation.
• - Enough space for lengthy names / job titles (for example, a job title could read "Directory of Human Resources" or "V.P. of Governmental Affairs"). We need this to look clean, whether the title be short (CEO) or long (as described above).

```html
<!DOCTYPE html>
<html lang="en">
<head>
<meta charset="utf-8">
<title>Vantrell Forge Works – Business Card</title>
<link href="https://fonts.googleapis.com/css2?family=Roboto:wght@400;500;700;900&display=swap" rel="stylesheet">
<style>
  :root {
    --brand-blue: #2f74b4;
    --deep-blue: #0355a3;
    --light-blue: #85abd2;
    --ink: #4a4a4a;
    --rule: #9a9a9a;
    --paper: #f4f4f4;
    --black: #111111;
    --backdrop: #2a2a2a;
  }
  * { margin: 0; padding: 0; box-sizing: border-box; }
  html, body { width: 1200px; height: 900px; overflow: hidden; }
  body {
    background: var(--backdrop);
    font-family: "Roboto", Arial, sans-serif;
    display: flex;
    flex-direction: column;
    align-items: center;
    justify-content: center;
    gap: 30px;
  }
  .card { width: 720px; height: 411px; position: relative; overflow: hidden; }

  /* Back side */
  .card-back {
    background: linear-gradient(135deg, var(--deep-blue) 0%, var(--brand-blue) 100%);
    display: flex;
    align-items: center;
    justify-content: center;
    gap: 28px;
  }
  .back-mark { display: flex; align-items: center; gap: 14px; }
  .mark-square { width: 34px; height: 34px; background: #ffffff; }
  .mark-name { color: #ffffff; font-weight: 900; font-size: 64px; letter-spacing: 1px; }
  .company-stack {
    color: #ffffff; font-weight: 700; font-size: 20px; line-height: 1.15;
    text-transform: uppercase; letter-spacing: 0.5px;
    border-left: 2px solid var(--light-blue); padding-left: 18px;
  }

  /* Front side */
  .card-front { background: var(--paper); }
  .person { position: absolute; left: 56px; top: 50px; }
  .person-name { color: var(--brand-blue); font-weight: 700; font-size: 32px; }
  .person-title { color: var(--ink); font-size: 17px; margin-top: 4px; }
  .front-mark { position: absolute; right: 56px; top: 58px; display: flex; align-items: center; gap: 10px; }
  .front-mark .mark-square { width: 22px; height: 22px; background: var(--brand-blue); }
  .front-mark .mark-name { color: var(--brand-blue); font-size: 44px; }
  .divider { position: absolute; left: 56px; right: 56px; top: 150px; height: 1px; background: var(--rule); }
  .contacts { position: absolute; left: 56px; top: 172px; list-style: none; }
  .contacts li { display: flex; align-items: center; gap: 12px; color: var(--ink); font-size: 16px; height: 27px; }
  .contacts svg { width: 15px; height: 15px; fill: var(--brand-blue); }
  .address { position: absolute; right: 56px; top: 186px; text-align: right; color: var(--ink); font-size: 16px; line-height: 1.6; }
  .address .web { color: var(--brand-blue); }
  .band-blue { position: absolute; left: 0; bottom: 0; width: 300px; height: 26px; background: var(--deep-blue); }
  .band-black { position: absolute; left: 300px; bottom: 0; width: 420px; height: 10px; background: var(--black); }
  .band-step { position: absolute; left: 300px; bottom: 10px; width: 10px; height: 16px; background: var(--black); }
</style>
</head>
<body>
  <section class="card card-back" aria-label="Card back">
    <div class="back-mark">
      <span class="mark-square"></span>
      <span class="mark-name">Vantrell</span>
    </div>
    <div class="company-stack">Vantrell<br>Forge<br>Works, Inc.</div>
  </section>

  <section class="card card-front" aria-label="Card front">
    <div class="person">
      <div class="person-name">Dorian Pelkey</div>
      <div class="person-title">V.P. of Governmental Affairs</div>
    </div>
    <div class="front-mark">
      <span class="mark-square"></span>
      <span class="mark-name">Vantrell</span>
    </div>
    <div class="divider"></div>
    <ul class="contacts">
      <li><svg viewBox="0 0 16 16" aria-hidden="true"><path d="M3 1l3 0 1.5 4-2 1.3a9 9 0 0 0 4.2 4.2L11 8.5l4 1.5v3a2 2 0 0 1-2 2A12 12 0 0 1 1 3a2 2 0 0 1 2-2z"/></svg>555 014 2286</li>
      <li><svg viewBox="0 0 16 16" aria-hidden="true"><path d="M4 0h8a1 1 0 0 1 1 1v14a1 1 0 0 1-1 1H4a1 1 0 0 1-1-1V1a1 1 0 0 1 1-1zm1 2v10h6V2zm3 11a1 1 0 1 0 0 2 1 1 0 0 0 0-2z"/></svg>555 017 4410</li>
      <li><svg viewBox="0 0 16 16" aria-hidden="true"><path d="M4 0h7v4H4zM1 5h14v7h-3v4H4v-4H1zm5 7v2h4v-2z"/></svg>555 017 4411</li>
      <li><svg viewBox="0 0 16 16" aria-hidden="true"><path d="M0 3h16v10H0zm1.5 1.2V5l6.5 4 6.5-4v-.8z"/></svg>info@vantrellforge.com</li>
    </ul>
    <div class="address">
      Level 2, 17 Harlow Lane<br>
      Kestrel Bay, VIC 3999<br>
      <span class="web">www.vantrellforge.com</span>
    </div>
    <div class="band-blue"></div>
    <div class="band-step"></div>
    <div class="band-black"></div>
  </section>
</body>
</html>
```